Paperwell Solutions Services Flyer

Create a 2 sided A4 flyer/PDF of the services we offer and a description of each etc.
Details can be found at: https://www.paperwell-solutions.co.uk/
Main services: Document Scanning, Invoice Processing and other services we offer.

Industry/Entity Type

Document Management

Font styles to use
Other font styles liked:
• Montserrat

Colors

Designer to choose colors to be used in the design.

Requirements
Must have
• Document Scanning, Box Storage, Invoice Processing, Book Scanning, Large format scanning
Nice to have
• Colourful d/s flyer listing our services with a brief description on each

```html
<!DOCTYPE html>
<html lang="en">
<head>
<meta charset="utf-8">
<title>Paperwell Solutions Services Flyer</title>
<link href="https://fonts.googleapis.com/css2?family=Poppins:wght@400;500;600;700&display=swap" rel="stylesheet">
<style>
:root{
  --red:#c8161d;
  --red-deep:#a80f15;
  --ink:#2c2c2e;
  --text:#1f1f1f;
  --panel:#e5e5e6;
  --cell:#d9d9db;
  --stage:#b5b5b5;
  --white:#ffffff;
}
*{margin:0;padding:0;box-sizing:border-box}
html,body{width:1200px;height:1200px;overflow:hidden}
body{background:var(--stage);font-family:'Poppins',sans-serif;color:var(--text);position:relative}
.page{position:absolute;width:860px;height:1217px;background:var(--white);transform:scale(.6216);transform-origin:0 0;overflow:hidden}
.page--front{left:44.8px;top:206.4px}
.page--back{left:614.8px;top:206.4px}
.abs{position:absolute}
.red{color:var(--red)}

/* front hero */
.brand{left:65px;top:78px;display:flex;align-items:center;gap:10px;color:var(--ink);font-weight:600;font-size:24px;line-height:30px;white-space:nowrap}
.brand__mark{width:16px;height:16px;background:var(--red);flex:none}
.hero-dark{left:451px;top:290px;width:409px;height:155px;background:var(--ink)}
.hero-white{left:451px;top:0;width:409px;height:352px;background:var(--white);border-bottom-right-radius:70px}
.hero-red{left:0;top:150px;width:451px;height:294px;background:var(--red);border-bottom-right-radius:40px;overflow:hidden}
.hero-red__lower{position:absolute;left:0;top:195px;width:100%;height:100px;background:var(--red-deep)}
.hero-title{left:62px;top:168px;color:var(--white);font-weight:700;font-size:47px;line-height:49px}
.hero-intro{left:62px;top:357px;width:350px;color:var(--white);font-size:12.5px;line-height:15.5px;font-weight:500}
.hero-photo{left:395px;top:50px;width:425px;height:282px;border-radius:6px;background:linear-gradient(135deg,#f4f4f4 0%,#dcdcdc 55%,#2a2a2a 56%,#3a3a3a 70%,#e8e8e8 71%)}
.main-services{left:492px;top:360px;color:var(--white)}
.main-services h3{font-weight:400;font-size:19px;letter-spacing:.3px}
.main-services h3 b{color:var(--red);font-weight:600}
.svc{position:absolute;top:32px;display:flex;gap:10px;align-items:center;font-weight:600;font-size:15.5px;line-height:19px;white-space:nowrap}
.svc svg{width:38px;height:38px}

.section-title{left:70px;top:462px;width:720px;display:flex;align-items:center;gap:10px;font-weight:700;font-size:22px}
.section-title::before,.section-title::after{content:"";flex:1;height:1.5px;background:#555}
.col{width:330px}
.col h4{font-size:14.5px;font-weight:600;margin-bottom:8px}
.col p{font-size:11.2px;line-height:13.8px}

.benefits{left:63px;top:619px;width:734px;height:230px;background:var(--panel);border-radius:12px}
.tab{left:215px;top:619px;width:430px;height:38px}
.tab-label{left:215px;top:628px;width:430px;text-align:center;color:var(--white);font-weight:600;font-size:15px}
.benefits-lead{left:63px;top:667px;width:734px;text-align:center;font-weight:600;font-size:14px}
.cell{position:absolute;height:46px;background:var(--cell);border-radius:4px;font-size:11.5px;line-height:13.5px;display:flex;align-items:center;padding-left:13px}
.tick{position:absolute;width:14px;height:14px;z-index:2}
.cta{left:238px;top:815px;width:384px;height:34px;background:var(--red);border-radius:6px 6px 0 0;color:var(--white);font-weight:600;font-size:14.5px;text-align:center;line-height:34px}

.how{left:63px;top:876px;width:734px;height:230px;border:2px solid #9a9a9a;border-radius:10px}
.how-title{left:355px;top:864px;padding:0 8px;background:var(--white);font-weight:700;font-size:19px}
.step{position:absolute;top:945px;width:86px}
.step h5{font-size:12.5px;font-weight:600;line-height:15px;margin-bottom:4px}
.step p{font-size:10.6px;line-height:13px}
.step-icon{position:absolute;top:902px;width:38px;height:38px}
.step-arrow{position:absolute;top:913px;width:46px;height:14px}
.step-rule{position:absolute;top:952px;width:1px;height:140px;background:#c8c8c8}

.footer-phone{top:1128px;left:63px;width:197px;height:38px;background:var(--ink);color:var(--white);font-weight:700;font-size:22px;display:flex;align-items:center;gap:6px;padding-left:10px}
.footer-addr{top:1128px;left:280px;font-size:13.5px;line-height:16px;display:flex;gap:8px}
.footer-web{top:1124px;font-size:13.5px;line-height:19px}
.footer-web div{display:flex;gap:6px;align-items:center}
.ic{width:14px;height:14px;flex:none}

/* back */
.back-red{left:0;top:0;width:520px;height:282px}
.back-title{left:52px;top:40px;font-weight:700;line-height:1}
.back-title .l1{font-size:37px;color:var(--ink)}
.back-title .l2{font-size:60px;color:var(--white);margin-top:6px}
.back-title .l3{font-size:44px;color:var(--white);margin-top:2px;font-weight:600}
.machine{left:445px;top:28px;width:365px;height:240px;border-radius:6px;background:linear-gradient(180deg,#eef0f2 0%,#d6d9dc 45%,#8d9096 60%,#6f7278 100%)}
.back-intro{left:55px;top:296px;width:760px;font-size:14.8px;line-height:18px}
.thumb{position:absolute;top:355px;width:168px;height:125px;border:3px solid #fff;box-shadow:0 1px 4px rgba(0,0,0,.3);border-radius:6px}
.feat-head{left:57px;top:506px;font-weight:700;font-size:20px;line-height:24px}
.feat-list{left:57px;top:572px;list-style:none}
.feat-list li{display:flex;align-items:center;gap:9px;font-size:15px;font-weight:500;height:37.6px}
.feat-list svg{width:15px;height:15px}
.book{left:61px;top:803px;width:310px;height:267px;background:var(--panel);border-radius:10px;overflow:hidden}
.book-tab{left:61px;top:803px;width:250px;height:50px}
.book-label{left:84px;top:814px;color:var(--white);font-weight:700;font-size:20px}
.book-text{left:86px;top:870px;width:262px;font-size:13.6px;line-height:15.6px}
.other-head{left:435px;top:506px;font-weight:700;font-size:20px}
.other{position:absolute;left:435px;width:370px}
.other svg{position:absolute;left:0;top:-2px;width:38px;height:38px}
.other h5{margin-left:49px;font-size:14px;font-weight:700;line-height:17px}
.other p{margin-left:49px;font-size:11.6px;line-height:14px;margin-top:1px}
.divider{left:61px;top:1100px;width:749px;height:2px;background:#9a9a9a}
</style>
</head>
<body>
<svg width="0" height="0" style="position:absolute">
  <defs>
    <symbol id="tick" viewBox="0 0 16 16"><circle cx="8" cy="8" r="6.6" fill="none" stroke="#c8161d" stroke-width="1.6"/><path d="M5 8.2l2 2 4-4.2" fill="none" stroke="#c8161d" stroke-width="1.6"/></symbol>
    <symbol id="ring-dark" viewBox="0 0 40 40"><circle cx="20" cy="20" r="17.5" fill="#fff" stroke="#3a3a3c" stroke-width="3"/><rect x="13" y="11" width="14" height="18" rx="1.5" fill="none" stroke="#3a3a3c" stroke-width="1.6"/><path d="M16 16h8M16 20h8M16 24h5" stroke="#3a3a3c" stroke-width="1.4"/></symbol>
    <symbol id="ring-red" viewBox="0 0 40 40"><circle cx="20" cy="20" r="17.5" fill="#fff" stroke="#c8161d" stroke-width="3"/><rect x="13" y="11" width="14" height="18" rx="1.5" fill="none" stroke="#3a3a3c" stroke-width="1.6"/><path d="M16 16h8M16 20h8M16 24h5" stroke="#3a3a3c" stroke-width="1.4"/></symbol>
    <symbol id="chev" viewBox="0 0 46 14"><path d="M0 1l5 6-5 6h4l5-6-5-6zM8 1l5 6-5 6h4l5-6-5-6zM16 1l5 6-5 6h4l5-6-5-6z" fill="#c8161d"/><path d="M26 5h12V1l8 6-8 6V9H26z" fill="#444"/></symbol>
    <symbol id="phone" viewBox="0 0 16 16"><path d="M3.5 1.5l2.5 0 1 3.5-1.7 1.2c.8 1.8 2.2 3.2 4 4l1.2-1.7 3.5 1v2.5c0 .8-.7 1.5-1.5 1.5C7 13.5 2 8.5 2 3c0-.8.7-1.5 1.5-1.5z" fill="#c8161d"/></symbol>
    <symbol id="pin" viewBox="0 0 16 20"><path d="M8 1a6 6 0 0 0-6 6c0 4.5 6 12 6 12s6-7.5 6-12a6 6 0 0 0-6-6zm0 8.5A2.5 2.5 0 1 1 8 4.5a2.5 2.5 0 0 1 0 5z" fill="#c8161d"/></symbol>
    <symbol id="mail" viewBox="0 0 16 16"><rect x="1" y="3" width="14" height="10" fill="#c8161d"/><path d="M1 3l7 6 7-6" fill="none" stroke="#fff" stroke-width="1.3"/></symbol>
    <symbol id="globe" viewBox="0 0 16 16"><circle cx="8" cy="8" r="6.3" fill="none" stroke="#c8161d" stroke-width="1.4"/><path d="M1.7 8h12.6M8 1.7c-3 3.5-3 9 0 12.6M8 1.7c3 3.5 3 9 0 12.6" fill="none" stroke="#c8161d" stroke-width="1.1"/></symbol>
  </defs>
</svg>

<!-- FRONT -->
<section class="page page--front">
  <div class="abs brand"><span class="brand__mark"></span>Paperwell Solutions</div>
  <div class="abs hero-dark"></div>
  <div class="abs hero-white"></div>
  <div class="abs hero-red"><div class="hero-red__lower"></div></div>
  <div class="abs hero-photo" role="img" aria-label="Photo of a high-volume desktop document scanner"></div>
  <h1 class="abs hero-title">Document<br>Automation<br>Services</h1>
  <p class="abs hero-intro">At Paperwell Solutions, we deliver award-winning document automation services, from business process optimisation and document management to data capture and document scanning.</p>
  <div class="abs main-services">
    <h3>OUR <b>MAIN SERVICES</b></h3>
    <div class="svc" style="left:0"><svg viewBox="0 0 40 40"><rect x="6" y="6" width="22" height="28" rx="2" fill="#fff"/><path d="M10 13h14M10 18h14M10 23h10" stroke="#2f6fb5" stroke-width="2"/><circle cx="28" cy="28" r="7" fill="#c8161d"/></svg>Document<br>Scanning</div>
    <div class="svc" style="left:152px"><svg viewBox="0 0 40 40"><rect x="8" y="5" width="22" height="28" rx="2" fill="#fff"/><rect x="8" y="5" width="22" height="6" fill="#c8161d"/><path d="M12 16h14M12 21h14M12 26h9" stroke="#2f6fb5" stroke-width="2"/></svg>Invoice<br>Processing</div>
  </div>

  <h2 class="abs section-title"><span><span class="red">DOCUMENT</span> SCANNING</span></h2>
  <div class="abs col" style="left:64px;top:503px">
    <h4>High Volume Document Scanning Services</h4>
    <p>Paperwell Solutions provides high-quality document scanning services tailored to businesses of all sizes. Whether you're looking to digitise a single department's files or undertake a large-scale bulk scanning project.</p>
  </div>
  <div class="abs col" style="left:451px;top:501px;width:345px">
    <h4>Why Choose Paperwell Solutions?</h4>
    <p>With decades of experience, Paperwell Solutions has built a reputation as a trusted document scanning company. We use cutting-edge technology to provide a wide range of services, from high-volume scanning to specialised A3 scanning and large format digitisation.</p>
  </div>

  <div class="abs benefits"></div>
  <svg class="abs tab" viewBox="0 0 430 38"><path d="M0 0h430l-34 38H34z" fill="#2c2c2e"/></svg>
  <div class="abs tab-label">BENEFITS OF DIGITISING YOUR ARCHIVES</div>
  <p class="abs benefits-lead">Partnering with Paperwell Solutions delivers significant advantages for your business:</p>
  <div class="cell" style="left:87px;top:700px;width:231px">Digitise documents for easier<br>access from any location</div>
  <div class="cell" style="left:333px;top:700px;width:219px">Automate workflows for improved<br>productivity and efficiency.</div>
  <div class="cell" style="left:566px;top:700px;width:210px">Protect your data with secure<br>digital backups.</div>
  <div class="cell" style="left:87px;top:754px;width:231px">Preserve fragile or historic materials<br>with professional digitisation</div>
  <div class="cell" style="left:333px;top:754px;width:219px">Eliminate physical document<br>searches, saving time</div>
  <div class="cell" style="left:566px;top:754px;width:210px">Gain valuable insights through<br>searchable digital archives.</div>
  <svg class="tick" style="left:80px;top:716px"><use href="#tick"/></svg>
  <svg class="tick" style="left:326px;top:716px"><use href="#tick"/></svg>
  <svg class="tick" style="left:559px;top:716px"><use href="#tick"/></svg>
  <svg class="tick" style="left:80px;top:770px"><use href="#tick"/></svg>
  <svg class="tick" style="left:326px;top:770px"><use href="#tick"/></svg>
  <svg class="tick" style="left:559px;top:770px"><use href="#tick"/></svg>
  <div class="abs cta">Free up office space by storing files digitally</div>

  <div class="abs how"></div>
  <div class="abs how-title red">HOW IT WORKS</div>

  <svg class="step-icon" style="left:83px"><use href="#ring-dark"/></svg>
  <svg class="step-arrow" style="left:128px"><use href="#chev"/></svg>
  <svg class="step-icon" style="left:180px"><use href="#ring-red"/></svg>
  <svg class="step-arrow" style="left:232px"><use href="#chev"/></svg>
  <svg class="step-icon" style="left:295px"><use href="#ring-dark"/></svg>
  <svg class="step-arrow" style="left:340px"><use href="#chev"/></svg>
  <svg class="step-icon" style="left:393px"><use href="#ring-red"/></svg>
  <svg class="step-arrow" style="left:441px"><use href="#chev"/></svg>
  <svg class="step-icon" style="left:501px"><use href="#ring-dark"/></svg>
  <svg class="step-arrow" style="left:553px"><use href="#chev"/></svg>
  <svg class="step-icon" style="left:611px"><use href="#ring-red"/></svg>
  <svg class="step-arrow" style="left:662px"><use href="#chev"/></svg>
  <svg class="step-icon" style="left:721px"><use href="#ring-dark"/></svg>

  <div class="step-rule" style="left:171px"></div>
  <div class="step-rule" style="left:283px"></div>
  <div class="step-rule" style="left:385px"></div>
  <div class="step-rule" style="left:491px"></div>
  <div class="step-rule" style="left:599px"></div>
  <div class="step-rule" style="left:706px"></div>

  <div class="step" style="left:82px"><h5>Document<br>Survey</h5><p>Arrange a site visit to evaluate your documents and gather information about project requirements.</p></div>
  <div class="step" style="left:180px;width:95px"><h5>Collection</h5><p>Our transport team will collect your documents using GP tracked vehicles ensuring secure delivery to our processing centre.</p></div>
  <div class="step" style="left:296px"><h5>Document<br>Scanning</h5><p>Documents are scanned using Arlo, Vexis, Plenar and Stellan equipment.</p></div>
  <div class="step" style="left:389px;width:95px"><h5>Image Quality<br>Assurance</h5><p>Every image is inspected by our independent Quality Assurance Team a key step that sets us apart.</p></div>
  <div class="step" style="left:499px;width:92px"><h5>Indexing</h5><p>Indexing data is assigned to digitised documents using OCR, data entry, barcode recognition and database lookup.</p></div>
  <div class="step" style="left:612px;width:90px"><h5>Validation</h5><p>Indexing data is validated independently by our Quality Assurance Team, separate from the indexing stage.</p></div>
  <div class="step" style="left:718px;width:70px"><h5>Data<br>Delivery</h5><p>Data will be securely transferred to you or hosted via LedgerView.</p></div>

  <div class="abs footer-phone"><svg class="ic"><use href="#phone"/></svg>01632 960418</div>
  <div class="abs footer-addr"><svg class="ic" style="height:18px"><use href="#pin"/></svg><span>Fernbank House, Millbrook<br>Way, Ashdale, West Sussex AS1 4QT</span></div>
  <div class="abs footer-web" style="left:565px"><div><svg class="ic"><use href="#mail"/></svg>sales@paperwell.co.uk</div><div><svg class="ic"><use href="#globe"/></svg>www.paperwell-solutions.co.uk</div></div>
</section>

<!-- BACK -->
<section class="page page--back">
  <svg class="abs back-red" viewBox="0 0 520 282"><path d="M0 0h470v220c0 30 15 55 40 62H0z" fill="#c8161d"/></svg>
  <div class="abs machine" role="img" aria-label="Photo of an industrial high-speed invoice scanning machine"></div>
  <h1 class="abs back-title"><div class="l1">Streamline Supplier</div><div class="l2">Invoice<br>Processing</div><div class="l3">with Automation</div></h1>
  <p class="abs back-intro">In today's fast-paced business environment, time is money. Yet, many companies still rely on manual processes for managing supplier invoices – processes that are slow, error-prone, and difficult to track.</p>
  <div class="thumb" style="left:56px;background:linear-gradient(160deg,#f2ece4,#9a948e 60%,#5a5650)" role="img" aria-label="Photo of hands typing on a laptop"></div>
  <div class="thumb" style="left:245px;background:linear-gradient(90deg,#d8d8d8,#3a3a3a 40%,#eeeeee 60%,#2f2f2f)" role="img" aria-label="Photo of office files in box folders"></div>
  <div class="thumb" style="left:433px;background:linear-gradient(120deg,#8a6a4a,#c9b48f 50%,#6b5a48)" role="img" aria-label="Photo of library shelves filled with books"></div>
  <div class="thumb" style="left:620px;background:linear-gradient(200deg,#eef0f2,#c9ccd0 60%,#e2661e 85%)" role="img" aria-label="Photo of architectural plans with a hard hat"></div>

  <h2 class="abs feat-head"><span class="red">KEY FEATURES OF CLEARLEDGER</span><br>AP AUTOMATION</h2>
  <ul class="abs feat-list">
    <li><svg><use href="#tick"/></svg>Automated Invoice Scanning</li>
    <li><svg><use href="#tick"/></svg>Data Capture &amp; Validation</li>
    <li><svg><use href="#tick"/></svg>Approval Workflows</li>
    <li><svg><use href="#tick"/></svg>Real-Time Visibility</li>
    <li><svg><use href="#tick"/></svg>Secure Archival</li>
    <li><svg><use href="#tick"/></svg>Seamless ERP Integration</li>
  </ul>

  <div class="abs book"></div>
  <svg class="abs book-tab" viewBox="0 0 250 50"><path d="M10 0h240l-40 50H0V10A10 10 0 0 1 10 0z" fill="#2c2c2e"/></svg>
  <div class="abs book-label">BOOK SCANNING</div>
  <p class="abs book-text">At Paperwell Solutions, our book scanning services are designed to deliver high-quality digital reproductions of your books while ensuring the utmost care for the original materials. Whether your project involves scanning a single rare volume or digitising an entire library, we employ advanced, non-destructive methods that cater to the specific needs of your collection.</p>

  <h2 class="abs other-head"><span class="red">OUR OTHER</span> SERVICES</h2>
  <div class="other" style="top:548px"><svg><use href="#ring-dark"/></svg><h5>BOX STORAGE</h5><p>Secure your critical records with our document storage services. We provide highly regulated storage facilities and robust cloud platforms.</p></div>
  <div class="other" style="top:624px"><svg><use href="#ring-red"/></svg><h5>SECURE DOCUMENT DESTRUCTION</h5><p>Dispose of obsolete or sensitive documents securely with our certified destruction services. Our compliant processes ensure that your materials.</p></div>
  <div class="other" style="top:700px"><svg><use href="#ring-dark"/></svg><h5>DOCUMENT MANAGEMENT SYSTEMS</h5><p>Centralise and streamline your information with our feature-rich document management software. Consolidate documents from across.</p></div>
  <div class="other" style="top:775px"><svg><use href="#ring-red"/></svg><h5>DIGITAL MAILROOM</h5><p>Future-proof your business with our digital mailroom solutions. We digitise incoming mail and automate workflows, replacing outdated.</p></div>
  <div class="other" style="top:850px"><svg><use href="#ring-dark"/></svg><h5>MICROFILM DIGITISATION</h5><p>Preserve and access historical data with our expert microfilm digitisation services. We convert microfilm records into searchable.</p></div>
  <div class="other" style="top:928px"><svg><use href="#ring-red"/></svg><h5>WORKFLOW SYSTEMS</h5><p>Transform your operations with our tailored workflow systems. These solutions automate tasks, reduce manual intervention.</p></div>
  <div class="other" style="top:1008px"><svg><use href="#ring-dark"/></svg><h5>LARGE FORMAT SCANNING</h5><p>Our specialised large-format scanning services digitise oversized materials such as blueprints, maps, and posters.</p></div>

  <div class="abs divider"></div>
  <div class="abs footer-phone"><svg class="ic"><use href="#phone"/></svg>01632 960418</div>
  <div class="abs footer-addr"><svg class="ic" style="height:18px"><use href="#pin"/></svg><span>Fernbank House, Millbrook<br>Way, Ashdale, West Sussex AS1 4QT</span></div>
  <div class="abs footer-web" style="left:565px"><div><svg class="ic"><use href="#mail"/></svg>sales@paperwell.co.uk</div><div><svg class="ic"><use href="#globe"/></svg>www.paperwell-solutions.co.uk</div></div>
</section>
</body>
</html>
```